Dwelvano - "Where Pest Control is Free for Life..." Please see pitch deck...

Project goal, that this is a reusable template, not a one-off card
Brand and design direction, follow the logo, use the brand palette (with a color swatch table), typography and layout guidance
The John Doe placeholder content as a clean field-by-field table (name, title, company, address, office, cell, fax, email, dwelvano.com)
Print specs, 3.5 × 2 in trim, 0.125 in bleed, 300 DPI, CMYK, crop marks
Deliverables, layered editable PSD (your primary ask) plus vector .AI/.EPS and a press-ready PDF/X-1a, with fonts packaged
What you'll provide (logo, colors, fonts)
Process and sign-off, concept first, then full file package on approval.
Populate every field with this John Doe placeholder data so we can see the layout fully built out. We will replace it per person.
Name John Doe
Title Title / Position
Company Dwelvano
Address 123 Main Street, Suite 100, Tallahassee, FL 32301
Office (850) 555-0100
Cell (850) 555-0123
Fax (850) 555-0199
Email johndoe@dwelvano.com
Website dwelvano.com

We need the working, editable source files so we can update them ourselves, plus a ready-to-print export:
1. Photoshop (.PSD) — fully layered and editable, with each contact field on its own labeled text layer. This is the primary requested format.
2. Vector source — the press-standard editable format, Adobe Illustrator (.AI) and/or .EPS, since vector is preferred for crisp text and logos at print.
3. Print-ready PDF — press-quality (PDF/X-1a), CMYK, with bleed and crop marks, both sides.
4. Packaged fonts and links — include or list all fonts used, and package any linked assets so the files open correctly on our end.

Why both PSD and vector
The PSD covers our request directly and is easy for us to edit. Vector (.AI/.EPS) is what most commercial printers actually prefer for type and logos because it stays razor-sharp at any size. Providing both keeps us flexible no matter which printer we use. Have fun and keep it modern and cool the designer of the logo did a great job, see what you can do.

```html
<!DOCTYPE html>
<html lang="en">
<head>
<meta charset="utf-8">
<title>Dwelvano Business Card</title>
<link rel="stylesheet" href="https://fonts.googleapis.com/css2?family=Montserrat:wght@400;600;800&family=Lato:wght@400&display=swap">
<style>
  :root{
    --stage:#262627;
    --card:#1b1b1c;
    --teal:#0cb2c5;
    --white:#ffffff;
    --ink:#1b1b1c;
    --emboss:#2a2a2b;
  }
  *{margin:0;padding:0;box-sizing:border-box}
  html,body{width:1200px;height:1059px;overflow:hidden;background:var(--stage)}
  .canvas{position:relative;width:1200px;height:1059px}
  .card{position:absolute;background:var(--card);border-radius:24px;overflow:hidden}
  .card--front{left:256px;top:87px;width:690px;height:394px}
  .card--back{left:254px;top:547px;width:704px;height:401px}

  .wordmark{position:absolute;font-family:"Montserrat",sans-serif;font-weight:800;letter-spacing:-1px;line-height:1;display:flex;align-items:center;gap:10px}
  .card--front .wordmark{right:26px;top:40px;font-size:60px;color:var(--white)}
  .wordmark__square{width:16px;height:16px;background:var(--teal)}
  .card--back .wordmark{left:50%;top:50%;transform:translate(-50%,-50%);font-size:66px;color:var(--emboss)}

  .person{position:absolute;left:25px;top:212px;font-family:"Montserrat",sans-serif}
  .person__name{font-size:26px;font-weight:600;color:var(--teal);letter-spacing:0.5px;line-height:1}
  .person__title{font-size:17px;font-weight:400;color:var(--white);margin-top:10px}

  .divider{position:absolute;left:26px;top:276px;width:624px;height:1.5px;background:var(--white)}

  .contact{position:absolute;font-family:"Lato",sans-serif;font-size:18px;color:var(--white);line-height:1}
  .contact__row{display:flex;align-items:center;gap:8px;height:28px}
  .contact__icon{width:18px;height:18px;fill:var(--teal);flex:none}
  .contact--phones{left:24px;top:292px}
  .contact--online{left:201px;top:290px}
  .contact--online .contact__row{gap:12px}
  .contact--address{left:434px;top:295px;line-height:1.45}

  .band{position:absolute;left:0;bottom:0;width:690px;height:30px}
  .website{position:absolute;left:415px;right:0;bottom:6px;text-align:center;font-family:"Lato",sans-serif;font-size:18px;color:var(--ink)}
</style>
</head>
<body>
<main class="canvas">
  <section class="card card--front" aria-label="Business card front">
    <div class="wordmark"><span class="wordmark__square"></span>Dwelvano</div>

    <div class="person">
      <p class="person__name">JOHN DOE</p>
      <p class="person__title">Owner</p>
    </div>

    <div class="divider"></div>

    <div class="contact contact--phones">
      <div class="contact__row">
        <svg class="contact__icon" viewBox="0 0 24 24" aria-label="Office"><path d="M2 9c0-3 5-5 10-5s10 2 10 5v2h-5V8H7v3H2z"/><path d="M6 12h12l2 8H4z"/></svg>
        <span>(850) 555-0100</span>
      </div>
      <div class="contact__row">
        <svg class="contact__icon" viewBox="0 0 24 24" aria-label="Cell"><path d="M7 1h10a1 1 0 0 1 1 1v20a1 1 0 0 1-1 1H7a1 1 0 0 1-1-1V2a1 1 0 0 1 1-1zm1 3v14h8V4zm4 15.5a1.2 1.2 0 1 0 0 2.4 1.2 1.2 0 0 0 0-2.4z"/></svg>
        <span>(850) 555-0123</span>
      </div>
    </div>

    <div class="contact contact--online">
      <div class="contact__row">
        <svg class="contact__icon" viewBox="0 0 24 24" aria-label="Fax"><rect x="1" y="6" width="5" height="16"/><rect x="8" y="2" width="10" height="6"/><rect x="7" y="9" width="16" height="13"/></svg>
        <span>(850) 555-0199</span>
      </div>
      <div class="contact__row">
        <svg class="contact__icon" viewBox="0 0 24 24" aria-label="Email"><path d="M1 5h22v2l-11 7L1 7z"/><path d="M1 9l11 7 11-7v11H1z"/></svg>
        <span>johndoe@dwelvano.com</span>
      </div>
    </div>

    <address class="contact contact--address" style="font-style:normal">
      123 Main Street, Suite 100,<br>Tallahassee, FL 32301
    </address>

    <svg class="band" viewBox="0 0 690 30" preserveAspectRatio="none" aria-hidden="true">
      <polygon points="415,0 690,0 690,30 385,30" fill="var(--teal)"/>
      <polygon points="0,9 392,9 385,16 0,16" fill="var(--teal)"/>
      <polygon points="0,22 380,22 372,30 0,30" fill="var(--teal)"/>
    </svg>
    <p class="website">www.dwelvano.com</p>
  </section>

  <section class="card card--back" aria-label="Business card back">
    <div class="wordmark">Dwelvano</div>
  </section>
</main>
</body>
</html>
```